Website for new dental office

I am Dr. Colin Ashford and am building a new dental practice. I specialize in general dentistry. I am young and have a higher end dental practice incorporating very new technologies and would like my website to reflect that. As many dental patients are older, the website must be very easy to navigate. I would like patients to be able to request appointments, and will eventually add on patient information forms (the health history, etc, that you normally fill out in the practice) from my practice management software, so leave an area for that.

Industry/Entity Type

Building

```html
<!DOCTYPE html>
<html lang="en">
<head>
<meta charset="utf-8">
<title>Colin Ashford, DDS</title>
<link href="https://fonts.googleapis.com/css2?family=Open+Sans:wght@300;400;600;700&family=Montserrat:wght@500&family=Arimo&display=swap" rel="stylesheet">
<style>
:root{
  --ink:#2b2b2b;
  --muted:#6a6a6a;
  --blue:#7a92d6;
  --slate:#5c6990;
  --orange:#f59a24;
  --tan:#b9a37d;
  --page:#e9eef1;
  --panel:#d7dee3;
  --field:#f6f8f9;
  --footer:#0f0f0f;
  --footer-bar:#222;
  --white:#fff;
}
*{box-sizing:border-box;margin:0;padding:0}
html,body{width:857px;height:1200px;overflow:hidden}
body{font-family:"Open Sans",sans-serif;color:var(--ink);background:var(--page);position:relative}
.abs{position:absolute}
.topline{left:0;top:0;width:857px;height:3px;background:#333}
.header{left:0;top:3px;width:857px;height:92px;background:linear-gradient(#fafafa,#eeeeee)}
.brand{left:64px;top:33px;font-size:25px;font-weight:600;letter-spacing:.5px;color:#3a3a3a;white-space:nowrap}
.cta{left:598px;top:12px;width:181px;height:32px;background:linear-gradient(#ffad3d,var(--orange));border:1px solid #d9801a;border-radius:2px;font-size:11px;color:#3a2200;display:flex;align-items:center;justify-content:center;gap:6px;white-space:nowrap}
.cta b{font-weight:700}
.callline{left:480px;top:56px;width:298px;font-size:10.5px;color:#444;display:flex;justify-content:flex-end;align-items:center;gap:4px;white-space:nowrap}
.callline strong{font-size:14.5px;font-weight:400;color:#222;margin-left:4px}
.hero{left:0;top:95px;width:857px;height:305px;background:linear-gradient(90deg,var(--tan) 0%,#c0ad89 55%,#d8ceb7 75%,#cfc3aa 100%)}
.hero-photo{left:584px;top:120px;width:273px;height:270px;background:linear-gradient(180deg,#e7e1d4,#d6cbb6 60%,#c5b89d)}
.nav{left:78px;top:95px;width:699px;height:29px;background:var(--blue);display:flex;align-items:center;padding-left:13px;font-size:10.5px;color:var(--white);white-space:nowrap}
.nav span{margin-right:37.5px}
.nav .active{background:#111;padding:3px 7px;margin-right:32px;font-weight:600}
.headline{left:76px;top:204px;font-size:29px;font-weight:300;letter-spacing:-.8px;color:#222;white-space:nowrap}
.headline b{font-weight:600;letter-spacing:-.5px}
.subline{left:76px;top:241px;font-size:20px;letter-spacing:1px;color:#2a2a2a;white-space:nowrap}
.curve{left:0;top:370px}
.sec-title{font-size:15px;font-weight:400;color:#2b2b2b;background:var(--page);padding-right:6px;white-space:nowrap}
.rule{height:6px;background:repeating-linear-gradient(135deg,#cfd5d9 0 1px,transparent 1px 3px)}
.svc-sub{left:78px;top:469px;font-size:10.5px;color:#333}
.svc-sub small{display:block;font-size:8px;color:var(--muted)}
.svc-btn{left:78px;top:506px;width:146px;height:20px;background:var(--blue);color:var(--white);font-size:8.5px;padding:4px 5px;white-space:nowrap}
.icons{left:74px;top:540px;display:flex;gap:16px}
.icon{width:38px;text-align:center;font-size:7.5px;font-weight:600;color:#666}
.icon i{display:block;width:38px;height:38px;border-radius:50%;background:radial-gradient(circle at 40% 35%,#dcdcdc,#a9a9a9);margin-bottom:6px}
.svc-photo{left:250px;top:469px;width:293px;height:149px;border:3px solid #d2d7da;background:linear-gradient(120deg,#4f84c9,#8fb3dd 40%,#e0c3b3 60%,#d8e4f2)}
.svc-text{left:82px;top:634px;width:460px;font-family:Arimo,sans-serif;font-size:8.6px;line-height:13px;color:#777}
.field{left:586px;width:192px;height:29px;background:var(--field);border:1px solid #d9dee1;font-size:8.5px;color:#999;padding:8px 6px}
.submit{left:586px;top:649px;width:111px;height:30px;background:var(--slate);border:1px solid #4b567a;color:var(--white);font-size:12.5px;font-weight:600;text-align:center;line-height:28px}
.divider{left:82px;top:698px;width:696px;height:1px;background:#d6dce0}
.gallery{left:77px;top:723px;width:699px;height:191px;background:var(--panel)}
.card{top:744px;width:151px}
.card .ph{height:90px;border:3px solid #eef1f3}
.card h4{font-size:10px;font-weight:400;color:#7f90c8;margin:10px 0 4px 3px}
.card p{font-size:7.8px;line-height:10.5px;color:#333;margin-left:3px;width:145px}
.arrow{width:20px;height:20px;background:var(--blue);display:flex;align-items:center;justify-content:center}
.footer{left:0;top:950px;width:857px;height:250px;background:var(--footer);border-top:4px solid #2d2d2d}
.up{left:409px;top:937px;width:36px;height:36px;border-radius:50%;background:#555;display:flex;align-items:center;justify-content:center}
.f-brand{left:93px;top:978px;font-family:Montserrat,sans-serif;font-size:24px;font-weight:500;color:var(--white);white-space:nowrap}
.f-about{left:94px;top:1016px;width:240px;font-size:8.6px;line-height:15.7px;color:#eee}
.f-head{font-size:12.5px;color:var(--white);white-space:nowrap}
.f-links{left:406px;top:1014px;font-size:10px;color:#eee;line-height:20.9px;white-space:nowrap}
.f-links .cur{font-weight:700}
.f-contact{left:623px;top:1014px;font-size:10px;color:#eee;line-height:13.5px;white-space:nowrap}
.bottom{left:0;top:1174px;width:857px;height:26px;background:var(--footer-bar);color:#eee;font-size:9.5px;text-align:center;line-height:26px}
</style>
</head>
<body>
<div class="abs topline"></div>
<header class="abs header"></header>
<div class="abs brand">COLIN ASHFORD, DDS</div>
<div class="abs cta">
  <svg width="12" height="11" viewBox="0 0 12 11"><rect x="1" y="2" width="10" height="8" rx="1" fill="none" stroke="#3a2200" stroke-width="1.2"/><path d="M3 1v2M9 1v2M1 5h10" stroke="#3a2200" stroke-width="1.2"/></svg>
  <span>Request a <b>FREE</b> Consultation</span>
</div>
<div class="abs callline">
  <svg width="10" height="10" viewBox="0 0 10 10"><path d="M2 0.5l2 2-1 1.2c.6 1.3 1.6 2.3 2.8 2.8L7 5.5l2 2-1.2 1.7C4.5 9 1 5.5.8 1.7z" fill="#222"/></svg>
  <span>You call, we're there</span><strong>(555) 214-3890</strong>
</div>

<section class="abs hero"></section>
<div class="abs hero-photo" role="img" aria-label="Photo of the dentist in a white coat holding dental tools beside an exam lamp"></div>
<nav class="abs nav">
  <span class="active">Home</span><span>Our Team</span><span>Philosophy</span><span>Restorative</span><span>Cosmetic</span><span>Tooth Replacement</span><span>First Visit Contact</span>
</nav>
<h1 class="abs headline">I specialize in <b>General Dentistry</b></h1>
<p class="abs subline">Teeth Whitening Solutions for Everyone</p>
<svg class="abs curve" width="857" height="40" viewBox="0 0 857 40"><path d="M0 27 Q428 -22 857 27 L857 40 L0 40Z" fill="#e9eef1"/></svg>

<div class="abs" style="left:78px;top:439px;width:462px;display:flex;align-items:center">
  <h2 class="sec-title">Our Services</h2><div class="rule" style="flex:1"></div>
  <svg width="16" height="8" viewBox="0 0 16 8" style="margin-left:4px"><path d="M5 1L1 4l4 3zM11 1l4 3-4 3z" fill="#888"/></svg>
</div>
<div class="abs svc-sub">Teeth Protection<small>Lorem Ipsum is simply dummy text</small></div>
<div class="abs svc-btn">The Services show on Gallery</div>
<div class="abs icons">
  <div class="icon"><i></i>Restorative</div>
  <div class="icon"><i></i>Preventive</div>
  <div class="icon"><i></i>Replacement</div>
</div>
<div class="abs svc-photo" role="img" aria-label="Photo of a patient receiving a dental check-up"></div>
<p class="abs svc-text">Aliquam erat volutpat. Duis blandit augue ac orci laoreet eget condimentum magna venenatis. Maecenas eget augue in nisl malesuada mollis. Vivamus eget bibendum dolor. Nulla vel varius mi. In hac habitasse platea dictumst. Duis</p>

<div class="abs" style="left:584px;top:439px;width:194px;display:flex;align-items:center">
  <h2 class="sec-title">Request an Appointment</h2><div class="rule" style="flex:1"></div>
</div>
<div class="abs field" style="top:476px">Name</div>
<div class="abs field" style="top:511px">E-mail</div>
<div class="abs field" style="top:546px">Phone</div>
<div class="abs field" style="top:581px;height:57px">Message</div>
<div class="abs submit">Submit</div>

<div class="abs divider"></div>
<section class="abs gallery"></section>
<div class="abs arrow" style="left:73px;top:825px"><svg width="8" height="10" viewBox="0 0 8 10"><path d="M6 1L2 5l4 4" stroke="#fff" stroke-width="2" fill="none"/></svg></div>
<div class="abs arrow" style="left:760px;top:822px"><svg width="8" height="10" viewBox="0 0 8 10"><path d="M2 1l4 4-4 4" stroke="#fff" stroke-width="2" fill="none"/></svg></div>
<article class="abs card" style="left:100px"><div class="ph" role="img" aria-label="Photo of a smile while flossing" style="background:linear-gradient(135deg,#d99a8e,#f3ece8 55%,#c9776b)"></div><h4>Restorative</h4><p>Lorem Ipsum is simply dummy text of the printing and typesetting indus-try. Lorem</p></article>
<article class="abs card" style="left:266px"><div class="ph" role="img" aria-label="Photo of a bright smile with red lips" style="background:linear-gradient(160deg,#c8704e,#e9c9b0 45%,#b8453a)"></div><h4>Cosmetic</h4><p>Lorem Ipsum is simply dummy text of the printing and typesetting indus-try. Lorem</p></article>
<article class="abs card" style="left:430px"><div class="ph" role="img" aria-label="Photo of teeth with a dental mirror" style="background:linear-gradient(120deg,#d9575e,#eee 45%,#4d86d1)"></div><h4>Preventive</h4><p>Lorem Ipsum is simply dummy text of the printing and typesetting indus-try. Lorem</p></article>
<article class="abs card" style="left:598px"><div class="ph" role="img" aria-label="Photo of a set of dentures" style="background:radial-gradient(circle at 50% 50%,#e48d84,#f5f2f1 70%)"></div><h4>Replacement</h4><p>Lorem Ipsum is simply dummy text of the printing and typesetting indus-try. Lorem</p></article>

<footer class="abs footer"></footer>
<div class="abs up"><svg width="14" height="10" viewBox="0 0 14 10"><path d="M2 8l5-5 5 5" stroke="#fff" stroke-width="2.6" fill="none"/></svg></div>
<div class="abs f-brand">Colin Ashford, DDS</div>
<p class="abs f-about">Lorem Ipsum is simply dummy text of the printing and typesetting industry. Lorem Ipsum has been the industry's standard dummy text ever since the 1500s, when an unknown printer took a galley of type and scrambled</p>
<div class="abs f-links">
  <div class="f-head" style="margin:-16px 0 0">INVESTMENTS</div>
  <div class="cur" style="margin-top:2px">Home</div><div>Our Team</div><div>Philosophy</div><div>Restorative</div><div>Cosmetic</div><div>Tooth Replacement</div><div>First Visit Contact</div>
</div>
<div class="abs f-contact">
  <div class="f-head" style="margin:-16px 0 14px -4px">CONTACT US</div>
  <div>420 Harlow Crest Avenue</div>
  <div>Suite 300</div>
  <div style="margin-top:5px">Phone: (555) 214-3800</div>
  <div style="margin-top:5px">Fax: (555) 214-3800</div>
</div>
<div class="abs bottom">Copy Right © 2014 ColinAshford.dds. All Rights Reserved.</div>
</body>
</html>
```